Business card for a Exhibition booth fabrication company

Hi. My company would like to change our corporate name card. We are an events and Exhibition stand builder company. We would like our corporate name card to resonate what we do. I need someone to create something unique that relates to the industry that I am in. The graphic designer should be creative to incorporate the elements of my industry and try to blend in well in the design of the card. Our aim is to ensure that we are unique and our card can look different from our competitors.
Updates

Target Market(s)

Marketing and events manager from all companies

Contact Information for Business Card

The business card should have the following details:
Name
Job Title
Email
Website

Colors

Designer to choose colors to be used in the design.

Requirements
Must have
• The card must be look something that is relevant to the service that I am providing. My website is: www.velmora-buildworks.com
• You can see my website to get more information on what service that I am doing
Nice to have
• On the back of my card, I would like to have a globe image with the incorporation of my company logo. This is to indicate that my services can be done in any part of the world.

```html
<!DOCTYPE html>
<html lang="en">
<head>
<meta charset="utf-8">
<title>Velmora Buildworks – Business Card</title>
<link href="https://fonts.googleapis.com/css2?family=Arimo:wght@400;700&family=Lato:wght@400&display=swap" rel="stylesheet">
<style>
  :root {
    --backdrop-light: #dcdddf;
    --backdrop-dark: #a2a3a7;
    --card: #000000;
    --accent: #e31b23;
    --muted: #7a7a7a;
    --map-land: #262626;
    --map-edge: #111111;
    --brand-silver: #b9b9b9;
    --white: #ffffff;
  }
  * { margin: 0; padding: 0; box-sizing: border-box; }
  html, body { width: 1129px; height: 1200px; overflow: hidden; }
  body {
    position: relative;
    background: linear-gradient(90deg, var(--backdrop-light), var(--backdrop-dark));
    font-family: "Lato", sans-serif;
  }
  .card {
    position: absolute;
    width: 732px;
    height: 418px;
    background: var(--card);
    border-radius: 0 57px 0 57px;
    overflow: hidden;
  }
  .card--front { left: 116px; top: 141px; }
  .card--back { left: 318px; top: 629px; }

  .brand {
    position: absolute;
    left: 0;
    width: 416px;
    top: 198px;
    text-align: center;
    font-family: "Arimo", sans-serif;
    font-weight: 700;
    font-size: 25px;
    letter-spacing: 2px;
    color: var(--accent);
  }

  .person { position: absolute; left: 408px; top: 92px; }
  .person__name {
    font-family: "Arimo", sans-serif;
    font-weight: 700;
    font-size: 25px;
    letter-spacing: 0.5px;
    color: var(--accent);
    line-height: 30px;
  }
  .person__title {
    font-family: "Arimo", sans-serif;
    font-size: 20px;
    letter-spacing: 0.5px;
    color: var(--muted);
    line-height: 30px;
  }
  .divider {
    position: absolute;
    left: 408px;
    right: 0;
    top: 160px;
    height: 2px;
    background: var(--accent);
  }
  .address {
    position: absolute;
    left: 408px;
    top: 172px;
    font-size: 18px;
    line-height: 25px;
    color: var(--muted);
  }
  .contacts { position: absolute; left: 408px; top: 234px; list-style: none; }
  .contacts li {
    display: flex;
    align-items: center;
    height: 34px;
    font-size: 18px;
    color: var(--muted);
  }
  .contacts svg { width: 19px; height: 19px; margin-right: 12px; flex: none; }

  .world-map {
    position: absolute;
    left: 0;
    right: 0;
    top: 57px;
    height: 315px;
    background: radial-gradient(ellipse at 55% 45%, var(--map-land), var(--map-edge) 75%, var(--card));
  }
  .brand--back {
    position: absolute;
    left: 0;
    right: 0;
    top: 194px;
    text-align: center;
    font-family: "Arimo", sans-serif;
    font-weight: 700;
    font-size: 40px;
    letter-spacing: 3px;
    color: var(--brand-silver);
  }
  .site {
    position: absolute;
    left: 0;
    right: 0;
    top: 380px;
    text-align: center;
    font-size: 20px;
    letter-spacing: 4px;
    color: var(--white);
  }
</style>
</head>
<body>
  <section class="card card--front">
    <div class="brand">VELMORA BUILDWORKS</div>
    <div class="person">
      <div class="person__name">DANIEL HARCOURT</div>
      <div class="person__title">PRESIDENT</div>
    </div>
    <div class="divider"></div>
    <div class="address">Street Name, City Name<br>Zipcode - 01234</div>
    <ul class="contacts">
      <li>
        <svg viewBox="0 0 20 20" aria-hidden="true"><path d="M4 2l3 0 1.5 4-2 1.5a10 10 0 0 0 6 6l1.5-2 4 1.5v3a2 2 0 0 1-2 2A16 16 0 0 1 2 4a2 2 0 0 1 2-2z" fill="var(--accent)"/></svg>
        014-275-3390
      </li>
      <li>
        <svg viewBox="0 0 20 20" aria-hidden="true"><rect x="1" y="4" width="18" height="12" fill="var(--accent)"/><path d="M1 4l9 7 9-7" fill="none" stroke="#000" stroke-width="1.5"/></svg>
        info@velmora-buildworks.com
      </li>
      <li>
        <svg viewBox="0 0 20 20" aria-hidden="true" fill="none" stroke="var(--accent)" stroke-width="1.5"><circle cx="10" cy="10" r="8.5"/><ellipse cx="10" cy="10" rx="3.8" ry="8.5"/><path d="M1.5 10h17M3 5.5h14M3 14.5h14"/></svg>
        www.velmora-buildworks.com
      </li>
    </ul>
  </section>

  <section class="card card--back">
    <div class="world-map" role="img" aria-label="Dark grey world map spanning the card"></div>
    <div class="brand--back">VELMORA BUILDWORKS</div>
    <div class="site">www.velmora-buildworks.com</div>
  </section>
</body>
</html>
```